Web Developer Needs a Business Card Design

I need a personal business card design that represents me as a web developer for potential employers. I would like the background to be a dark color on the front for contrast with my logo and name. The back will have all my information along with a smaller version of the logo. I want something with a modern look and feel, not too conservative. This will be used for potential employers and freelance work.

Industry/Entity Type

Business

Contact Information for Business Card

Front should have my logo and name. The back should have all my personal information which would include: name: Tom Varulek, phone: 570-614-3098, email: tomvarulek@quillbox.net, website url: www.tomvarulek.net, logo, web developer.

Font styles to use
Sans Serif

Requirements
Must have
• Must include my logo. The color palette base color will be the logo color.

```html
<!DOCTYPE html>
<html lang="en">
<head>
<meta charset="utf-8">
<title>Tom Varulek – Business Card</title>
<link rel="stylesheet" href="https://fonts.googleapis.com/css2?family=Questrial&family=Arimo:wght@400&family=Roboto+Condensed:wght@300;400&display=swap">
<style>
  :root {
    --scene-bg: #2b2b2c;
    --card-bg: #232324;
    --card-edge: #1a1a1b;
    --brand-teal: #5fb3a0;
    --text-light: #d9d9d9;
    --text-soft: #bdbdbd;
    --divider: #9a9a9a;
  }
  * { margin: 0; padding: 0; box-sizing: border-box; }
  html, body {
    width: 1200px; height: 903px; overflow: hidden;
    background: var(--scene-bg);
  }
  .canvas { position: relative; width: 1200px; height: 903px; }

  .card {
    position: absolute;
    width: 520px; height: 297px;
    background: var(--card-bg);
    border: 1px solid var(--card-edge);
    border-radius: 3px;
  }
  .card--back { left: 80px; top: 110px; }
  .card--front { left: 600px; top: 496px; }

  /* brand mark: plain ring beside the name */
  .brand {
    position: absolute; left: 50%; transform: translateX(-50%);
    display: flex; align-items: center; gap: 10px;
    font-family: "Questrial", sans-serif;
    color: var(--brand-teal);
    white-space: nowrap;
  }
  .brand__ring {
    border: 4px solid var(--brand-teal);
    border-radius: 50%;
  }
  .card--back .brand { top: 28px; font-size: 18px; }
  .card--back .brand__ring { width: 54px; height: 54px; }
  .card--front .brand { top: 58px; font-size: 26px; }
  .card--front .brand__ring { width: 92px; height: 92px; border-width: 6px; }

  /* back side */
  .identity {
    position: absolute; right: 282px; bottom: 70px;
    text-align: right;
    font-family: "Questrial", sans-serif;
  }
  .identity__name { color: var(--brand-teal); font-size: 27px; letter-spacing: 1px; line-height: 1; }
  .identity__role { color: var(--text-soft); font-size: 16px; letter-spacing: 1px; margin-top: 2px; }

  .divider {
    position: absolute; left: 260px; top: 120px;
    width: 1px; height: 120px; background: var(--divider);
  }

  .contact {
    position: absolute; left: 282px; top: 136px;
    list-style: none;
    font-family: "Arimo", sans-serif; font-size: 15px;
    color: var(--text-light);
  }
  .contact__item { display: flex; align-items: center; gap: 9px; height: 28px; }
  .contact__icon { width: 11px; height: 11px; flex: none; }

  /* front side */
  .front-name {
    position: absolute; left: 0; right: 0; bottom: 46px;
    text-align: center;
    font-family: "Roboto Condensed", sans-serif; font-weight: 300;
    font-size: 42px; letter-spacing: 3px;
    color: var(--text-light);
  }
</style>
</head>
<body>
<main class="canvas">

  <section class="card card--back" aria-label="Business card, contact side">
    <div class="brand"><span class="brand__ring"></span><span class="brand__name">Tom Varulek</span></div>

    <div class="identity">
      <p class="identity__name">Tom Varulek</p>
      <p class="identity__role">web developer</p>
    </div>

    <span class="divider"></span>

    <ul class="contact">
      <li class="contact__item">
        <svg class="contact__icon" viewBox="0 0 12 12"><rect width="12" height="12" rx="2" fill="var(--brand-teal)"/><path d="M3.5 2.8l1.4 1.5-.7 1c.5 1 1.3 1.8 2.3 2.3l1-.7 1.5 1.4-.9 1c-2.8-.4-5-2.6-5.4-5.4z" fill="var(--card-bg)"/></svg>
        <span>570-614-3098</span>
      </li>
      <li class="contact__item">
        <svg class="contact__icon" viewBox="0 0 12 12"><rect width="12" height="12" rx="2" fill="var(--brand-teal)"/><rect x="2.5" y="3.5" width="7" height="5" fill="none" stroke="var(--card-bg)" stroke-width="1"/><path d="M2.5 3.5L6 6.3 9.5 3.5" fill="none" stroke="var(--card-bg)" stroke-width="1"/></svg>
        <span>tomvarulek@quillbox.net</span>
      </li>
      <li class="contact__item">
        <svg class="contact__icon" viewBox="0 0 12 12"><rect width="12" height="12" rx="2" fill="var(--brand-teal)"/><circle cx="6" cy="6" r="3.3" fill="none" stroke="var(--card-bg)" stroke-width="1"/><path d="M2.7 6h6.6M6 2.7c-1.4 1.8-1.4 4.8 0 6.6M6 2.7c1.4 1.8 1.4 4.8 0 6.6" fill="none" stroke="var(--card-bg)" stroke-width=".8"/></svg>
        <span>www.tomvarulek.net</span>
      </li>
    </ul>
  </section>

  <section class="card card--front" aria-label="Business card, front side">
    <div class="brand"><span class="brand__ring"></span><span class="brand__name">Tom Varulek</span></div>
    <h1 class="front-name">TOM VARULEK</h1>
  </section>

</main>
</body>
</html>
```